Website redesign for job agency recruitment

Please refer to the attached document, “Tarvenly Work Website Brief,” for comprehensive details regarding the scope, objectives, and requirements of this website redesign project.

For imagery you can use images from this website https://www.pixelmarrowfoto.com or any other you regularly use.

Target Market(s)

Jobseekers and Companies looking for general labour

Industry/Entity Type

Services: Oil, Gas and Mining, Administrative, Construction and Trades, Warehouse and Logistics and, Manufacturing.

Number of Pages Required

5+ page

Font styles to use
Serif
Other font styles liked:
• Inter, Open-Sans or similar.

Requirements
Must have
• The requirements highlighted in the Word document attached. The final design needs to be provided in Figma including all viewports (Desktop, mobiel and tablet)
Should not have
• Website we like as a reference: www.brevicktalentco.com, www.qelvaworks.com, www.zunmarra.com, www.ferrowhires.com, www.9vtalentpool.com, www.hiringwithtrello.ca

```html
<!DOCTYPE html>
<html lang="en">
<head>
<meta charset="utf-8">
<title>Tarvenly Work Agency – Service Pages</title>
<link rel="stylesheet" href="https://fonts.googleapis.com/css2?family=Inter:wght@400;500;600;700&family=Saira+Semi+Condensed:wght@500;600;700&display=swap">
<style>
:root{
  --board:#e9e9e9;
  --ink:#151515;
  --body:#3b3b3b;
  --navy:#0b2147;
  --navy-deep:#071833;
  --blue:#123c96;
  --yellow:#f5b800;
  --yellow-soft:#f7c938;
  --card:#f4f4f4;
  --card-line:#e4e4e4;
  --footer-text:#c3cde0;
}
*{margin:0;padding:0;box-sizing:border-box}
html,body{width:694px;height:1200px;overflow:hidden;background:var(--board)}
body{font-family:'Inter',sans-serif;color:var(--body)}
.board{position:relative;width:694px;height:1200px;background:var(--board);overflow:hidden}
.board-label{position:absolute;font:700 7.4px/1 'Inter',sans-serif;color:var(--ink);letter-spacing:.1px}
.page{position:absolute;width:297px;background:#fff;overflow:hidden}
.page > *{position:absolute}

/* header */
.topbar-phone{left:134px;top:0;width:84px;height:14px;background:var(--blue);clip-path:polygon(4px 0,100% 0,calc(100% - 4px) 100%,0 100%);display:flex;align-items:center;justify-content:center;gap:2px;color:#fff;font:500 3.5px/1 'Inter',sans-serif;white-space:nowrap}
.topbar-register{left:210px;top:0;width:87px;height:14px;background:var(--yellow);clip-path:polygon(4px 0,100% 0,100% 100%,0 100%);display:flex;align-items:center;justify-content:center;gap:3px;color:#2a2000;font:500 3.5px/1 'Inter',sans-serif;white-space:nowrap}
.brand{left:27px;top:9px;width:80px;display:flex;align-items:center;gap:2px}
.brand-dot{width:9px;height:9px;border-radius:50%;background:var(--blue);flex:none}
.brand-name{font:600 4.2px/1.15 'Inter',sans-serif;color:var(--blue);white-space:nowrap}
.main-nav{left:101px;top:22px;width:170px;display:flex;justify-content:space-between;font:600 3.6px/1 'Inter',sans-serif;color:var(--ink);white-space:nowrap}
.main-nav .is-active{color:var(--blue)}

/* hero */
.hero{left:0;top:33px;width:297px;height:60px}
.hero-title{left:27px;top:59px;font:600 8px/1 'Saira Semi Condensed',sans-serif;color:#fff;letter-spacing:.1px;white-space:nowrap}
.hero--warehouse{background:linear-gradient(90deg,#2f2a2a 0%,#4c3b33 30%,#7d5e43 55%,#b99572 78%,#d8c3a6 100%)}
.hero--manufacturing{background:linear-gradient(90deg,#1d4760 0%,#2f6681 35%,#7f8a6a 60%,#e49a2c 82%,#f0b048 100%)}
.hero--construction{background:linear-gradient(90deg,#5f5d58 0%,#857a66 35%,#c8a878 60%,#a9b6c3 85%,#c7d2dc 100%)}
.hero--admin{background:linear-gradient(90deg,#3c3c3c 0%,#707070 35%,#3a3c44 60%,#d5d2cd 80%,#5a5652 100%)}

/* headings and text */
.section-title{left:27px;font:600 8px/1 'Saira Semi Condensed',sans-serif;color:var(--ink);white-space:nowrap}
.highlight{background:var(--yellow);padding:0 1.5px;color:var(--ink)}
.lead{left:27px;width:244px;font:400 3.3px/6.2px 'Inter',sans-serif;color:var(--body)}
.lead b{font-weight:600;color:var(--ink)}

/* service cards */
.service-cards{left:27px;width:244px;height:21px;display:flex;gap:6px}
.service-card{flex:1;background:var(--card);border:.4px solid var(--card-line);display:flex;align-items:center;gap:4px;padding-left:5px;font:500 3.7px/1 'Inter',sans-serif;color:var(--ink);white-space:nowrap}
.service-card svg{width:10px;height:10px;flex:none}

/* content blocks */
.photo{width:112px;height:80px}
.photo-frame{border:.5px solid var(--yellow-soft)}
.block-title{font:600 6.4px/1 'Saira Semi Condensed',sans-serif;color:var(--ink);white-space:nowrap}
.block-text{font:400 3.4px/6.2px 'Inter',sans-serif;color:var(--body)}
.cta{width:57px;height:12px;background:var(--yellow);display:flex;align-items:center;justify-content:center;font:500 4px/1 'Inter',sans-serif;color:#1d1600;overflow:hidden;white-space:nowrap}
.cta::after{content:"";position:absolute;right:0;bottom:0;border-style:solid;border-width:0 0 8px 4px;border-color:transparent transparent var(--blue) transparent}

/* footer */
.site-footer{left:0;width:297px;height:103px;background:linear-gradient(180deg,var(--navy) 0%,#0c2650 60%,var(--navy-deep) 100%);color:var(--footer-text)}
.site-footer > *{position:absolute}
.footer-brand{left:22px;top:24px;width:50px;display:flex;flex-direction:column;align-items:center;gap:8px}
.footer-brand .brand-name{color:#fff;font-size:4.2px;text-align:center}
.footer-social{display:flex;gap:3px}
.footer-social span{width:7px;height:7px;border-radius:50%;border:.5px solid #c3cde0}
.footer-col{top:22px}
.footer-heading{font:600 4.2px/1 'Inter',sans-serif;color:#fff;white-space:nowrap}
.footer-heading::after{content:"";display:block;width:4px;height:.8px;background:var(--yellow);margin-top:3px}
.footer-links{list-style:none;margin-top:4px;font:400 3.2px/8.3px 'Inter',sans-serif;white-space:nowrap}
.footer-address{margin-top:4px;font:400 3.2px/1.5 'Inter',sans-serif;white-space:nowrap}
.footer-address li{display:flex;gap:3px;margin-bottom:3.4px;list-style:none}
.footer-address svg{width:5px;height:5px;flex:none;margin-top:.3px}
.footer-copy{left:0;top:92px;width:297px;text-align:center;font:400 3.1px/1 'Inter',sans-serif;color:var(--footer-text)}
</style>
</head>
<body>
<svg width="0" height="0" style="position:absolute">
  <defs>
    <symbol id="icon-phone" viewBox="0 0 24 24"><path d="M6.6 10.8a15 15 0 0 0 6.6 6.6l2.2-2.2a1 1 0 0 1 1-.25 11.4 11.4 0 0 0 3.6.57 1 1 0 0 1 1 1V20a1 1 0 0 1-1 1A17 17 0 0 1 3 4a1 1 0 0 1 1-1h3.5a1 1 0 0 1 1 1c0 1.25.2 2.45.57 3.57a1 1 0 0 1-.25 1z" fill="currentColor"/></symbol>
    <symbol id="icon-arrow" viewBox="0 0 24 12"><path d="M0 6h21M16 1l5 5-5 5" fill="none" stroke="currentColor" stroke-width="1.6"/></symbol>
    <symbol id="icon-temp" viewBox="0 0 24 24"><rect x="3" y="6" width="18" height="14" rx="1.5" fill="none" stroke="#f5b800" stroke-width="1.4"/><path d="M9 6V4h6v2" fill="none" stroke="#f5b800" stroke-width="1.4"/><circle cx="12" cy="13" r="4" fill="none" stroke="#f5b800" stroke-width="1.4"/><path d="M12 11v2.2l1.5 1" fill="none" stroke="#f5b800" stroke-width="1.2"/></symbol>
    <symbol id="icon-hire" viewBox="0 0 24 24"><rect x="2" y="5" width="15" height="12" rx="1.5" fill="none" stroke="#f5b800" stroke-width="1.4"/><path d="M7 5V3h5v2M2 10h15" fill="none" stroke="#f5b800" stroke-width="1.4"/><circle cx="17.5" cy="17" r="4.5" fill="#fff" stroke="#f5b800" stroke-width="1.4"/><path d="M15.5 17l1.5 1.5 2.5-3" fill="none" stroke="#f5b800" stroke-width="1.3"/></symbol>
    <symbol id="icon-perm" viewBox="0 0 24 24"><path d="M6 10a6 6 0 0 1 12 0z" fill="none" stroke="#f5b800" stroke-width="1.4"/><path d="M5 10h14" stroke="#f5b800" stroke-width="1.4"/><circle cx="12" cy="13.5" r="3" fill="none" stroke="#f5b800" stroke-width="1.4"/><path d="M4 22c1-4 4-5.5 8-5.5s7 1.5 8 5.5" fill="none" stroke="#f5b800" stroke-width="1.4"/></symbol>
    <symbol id="icon-building" viewBox="0 0 24 24"><path d="M4 22V3h11v19M15 9h5v13M2 22h20M7 7h2M11 7h2M7 11h2M11 11h2M7 15h2M11 15h2" fill="none" stroke="currentColor" stroke-width="1.5"/></symbol>
  </defs>
</svg>

<main class="board">
  <h2 class="board-label" style="left:51px;top:31px">WAREHOUSE &amp; LOGISTICS</h2>
  <h2 class="board-label" style="left:365px;top:31px">MANUFACTURING</h2>
  <h2 class="board-label" style="left:51px;top:609px">CONSTRUCTION &amp; TRADERS</h2>
  <h2 class="board-label" style="left:365px;top:609px">ADMINSTRATIVE</h2>

  <!-- Warehouse & Logistics page -->
  <article class="page" style="left:48px;top:50px;height:542px">
    <div class="brand"><span class="brand-dot"></span><span class="brand-name">Tarvenly Work Agency Ltd.</span></div>
    <div class="topbar-phone"><svg width="4" height="4"><use href="#icon-phone"/></svg>Toll Free: 1-888-555-0142</div>
    <div class="topbar-register">Client Registration <svg width="6" height="3"><use href="#icon-arrow"/></svg></div>
    <nav class="main-nav"><span>Home</span><span class="is-active">Services</span><span>Candidates</span><span>Employers</span><span>About Us</span><span>Contact Us</span></nav>
    <div class="hero hero--warehouse" role="img" aria-label="Warehouse aisle with a forklift moving stacked cartons"></div>
    <h1 class="hero-title">WAREHOUSE &amp; LOGISTICS</h1>

    <h2 class="section-title" style="top:105px">Elite Logistics <span class="highlight">Staffing</span></h2>
    <p class="lead" style="top:117px">Tarvenly Work Agency is a premiere Warehouse &amp; Logistics staffing agency that can provide you with a reliable and experienced workforce. We provide these positions.</p>
    <div class="service-cards" style="top:134px">
      <div class="service-card"><svg><use href="#icon-temp"/></svg>Temporary Positions</div>
      <div class="service-card"><svg><use href="#icon-hire"/></svg>Temporary-to-Hire</div>
      <div class="service-card"><svg><use href="#icon-perm"/></svg>Permanent Positions</div>
    </div>
    <h2 class="section-title" style="top:164px">We are Warehouse &amp; Logistics Staffing Advisors –</h2>
    <h2 class="section-title" style="top:176px"><span class="highlight">Time, Service and Budget</span></h2>
    <p class="lead" style="top:189px">As specialists for more than 10 years, we have met the highly labour-intensive staffing demands of Warehouse operators, carriers, and freight forwarders on-time and on-budget</p>

    <div class="photo-frame" style="left:32px;top:223px;width:112px;height:80px"></div>
    <div class="photo" style="left:27px;top:219px;background:linear-gradient(135deg,#8a5a3a,#3e5f8c 45%,#c9b18d 75%,#d9d9d9)" role="img" aria-label="Two managers reviewing documents in a warehouse aisle"></div>
    <h3 class="block-title" style="left:161px;top:210px">Companies</h3>
    <p class="block-text" style="left:161px;top:220px;width:110px">Whether you are looking for reliable, experienced Laborers to maintain a contingent workforce, or a Warehouse Supervisor with refrigeration experience, our recruiters are experts in providing a skilled workforce to get the job done right. Our registrant database includes tens of thousands of qualified personnel allowing us to respond quickly to your changing needs so you can maintain your service levels, turn over inventory, and hit your KPI's while staying in firm control over labour costs. Registered Candidates undergo extensive screening and we stand behind every person we place. We focus on the people while you focus on moving inventory and managing your business.</p>
    <div class="cta" style="left:161px;top:298px">Request Staffing</div>

    <h3 class="block-title" style="left:27px;top:325px">Warehouse &amp; Logistics Candidates</h3>
    <p class="block-text" style="left:27px;top:334px;width:112px">Tarvenly Work Agency is firmly entrenched in warehouses, distribution centers and terminals all over Canada. We invest our time and resources back into the Warehousing and Logistics community to ensure we maximize employment opportunities for you. Once your resume or bio is submitted, our team helps organize and prepare your profile while getting to know you. Our clients appreciate our industry expertise and the thorough screening process we do to ensure a good fit. We may be bit tougher with our expectations, but we also stand behind every person we place.</p>
    <div class="cta" style="left:27px;top:409px">Apply for jobs</div>
    <div class="photo-frame" style="left:154px;top:330px;width:112px;height:89px"></div>
    <div class="photo" style="left:159px;top:326px;height:89px;background:linear-gradient(135deg,#b9946a,#6d5340 40%,#e07a2c 60%,#3a3a3a)" role="img" aria-label="Three workers in safety vests talking between warehouse shelves"></div>

    <footer class="site-footer" style="top:439px">
      <div class="footer-brand"><span class="brand-name">Tarvenly Work Agency Ltd.</span><div class="footer-social"><span></span><span></span></div></div>
      <div class="footer-col" style="left:94px"><h4 class="footer-heading">Quick Links</h4><ul class="footer-links"><li>Home</li><li>Services</li><li>Candidates</li><li>Employers</li><li>About us</li><li>Contact us</li></ul></div>
      <div class="footer-col" style="left:147px"><h4 class="footer-heading">Our Services</h4><ul class="footer-links"><li>Oil, Gas and Mining</li><li>Administrative</li><li>Construction and Trades</li><li>Warehouse and Logistics</li><li>Manufacturing.</li></ul></div>
      <div class="footer-col" style="left:217px"><h4 class="footer-heading">Our Address</h4><ul class="footer-address"><li><svg><use href="#icon-building"/></svg>410 217 6 Ave SW Calgary,<br>AB, T2P 1K3</li><li><svg><use href="#icon-phone"/></svg>Toll-Free: 1-888-555-0142</li><li><svg><use href="#icon-phone"/></svg>403-555-0187</li></ul></div>
      <p class="footer-copy">© Tarvenly Work Agency Ltd. | All rights reserved 2026</p>
    </footer>
  </article>

  <!-- Manufacturing page -->
  <article class="page" style="left:365px;top:50px;height:542px">
    <div class="brand"><span class="brand-dot"></span><span class="brand-name">Tarvenly Work Agency Ltd.</span></div>
    <div class="topbar-phone"><svg width="4" height="4"><use href="#icon-phone"/></svg>Toll Free: 1-888-555-0142</div>
    <div class="topbar-register">Client Registration <svg width="6" height="3"><use href="#icon-arrow"/></svg></div>
    <nav class="main-nav"><span>Home</span><span class="is-active">Services</span><span>Candidates</span><span>Employers</span><span>About Us</span><span>Contact Us</span></nav>
    <div class="hero hero--manufacturing" role="img" aria-label="Gloved hands sorting produce on a factory conveyor line"></div>
    <h1 class="hero-title">MANUFACTURING</h1>

    <h2 class="section-title" style="top:105px">Precision Manufacturing <span class="highlight">Staffing</span></h2>
    <p class="lead" style="top:117px">Tarvenly Work Agency is a premiere Manufacturing &amp; Production staffing agency that can provide you with a reliable and experienced workforce. We provide these positions.</p>
    <div class="service-cards" style="top:134px">
      <div class="service-card"><svg><use href="#icon-temp"/></svg>Temporary Positions</div>
      <div class="service-card"><svg><use href="#icon-hire"/></svg>Temporary-to-Hire</div>
      <div class="service-card"><svg><use href="#icon-perm"/></svg>Permanent Positions</div>
    </div>
    <h2 class="section-title" style="top:164px">We are Manufacturing &amp; Production Staffing Advisors –</h2>
    <h2 class="section-title" style="top:176px"><span class="highlight">Quality, Time, Budget!</span></h2>
    <p class="lead" style="top:189px">As specialists for more than 10 years, we have met the staffing demands of small family-owned shops to some of Canada's largest manufacturing, industrial and processing companies, on-time and on-budget.</p>

    <div class="photo-frame" style="left:32px;top:220px;width:112px;height:80px"></div>
    <div class="photo" style="left:27px;top:216px;background:linear-gradient(135deg,#2f5aa0,#c24a2a 40%,#2b3f6e 65%,#bfc6cf)" role="img" aria-label="Smiling supervisor holding a tablet in a stockroom"></div>
    <h3 class="block-title" style="left:161px;top:210px">Companies</h3>
    <p class="block-text" style="left:161px;top:220px;width:110px">Whether you are looking for experienced Laborers to maintain a contingent workforce, or a Quality Control Manager with a Six Sigma black belt, our recruiters are experts in providing a skilled workforce to get the job done right. Our registrant database includes tens of thousands of qualified personnel, allowing us to respond quickly to your changing needs so you can maintain your quality levels and hit your KPIs while staying in firm control over labour costs. Candidates undergo extensive screening and we stand behind every person we place. We focus on the people while you focus on production</p>
    <div class="cta" style="left:161px;top:292px">Request Staffing</div>

    <h3 class="block-title" style="left:27px;top:319px">Manufacturing &amp; Production Candidates</h3>
    <p class="block-text" style="left:27px;top:328px;width:112px">Tarvenly Work Agency is firmly entrenched in Manufacturing &amp; Production facilities all over Canada. We invest our time and resources back into the community to ensure we maximize employment opportunities for you. Once your resume or bio is submitted, our team helps organize and prepare your profile while getting to know you. Our clients appreciate our industry expertise and the thorough screening process we do to ensure a good fit. We may be bit tougher with our expectations, but we also stand behind every person we place</p>
    <div class="cta" style="left:27px;top:403px">Apply for jobs</div>
    <div class="photo-frame" style="left:154px;top:324px;width:112px;height:89px"></div>
    <div class="photo" style="left:159px;top:320px;height:89px;background:linear-gradient(135deg,#8a98a8,#e9ecef 45%,#c9d2dc 70%,#6f7c8a)" role="img" aria-label="Two production workers in white caps at a bottling line"></div>

    <footer class="site-footer" style="top:439px">
      <div class="footer-brand"><span class="brand-name">Tarvenly Work Agency Ltd.</span><div class="footer-social"><span></span><span></span></div></div>
      <div class="footer-col" style="left:94px"><h4 class="footer-heading">Quick Links</h4><ul class="footer-links"><li>Home</li><li>Services</li><li>Candidates</li><li>Employers</li><li>About us</li><li>Contact us</li></ul></div>
      <div class="footer-col" style="left:147px"><h4 class="footer-heading">Our Services</h4><ul class="footer-links"><li>Oil, Gas and Mining</li><li>Administrative</li><li>Construction and Trades</li><li>Warehouse and Logistics</li><li>Manufacturing.</li></ul></div>
      <div class="footer-col" style="left:217px"><h4 class="footer-heading">Our Address</h4><ul class="footer-address"><li><svg><use href="#icon-building"/></svg>410 217 6 Ave SW Calgary,<br>AB, T2P 1K3</li><li><svg><use href="#icon-phone"/></svg>Toll-Free: 1-888-555-0142</li><li><svg><use href="#icon-phone"/></svg>403-555-0187</li></ul></div>
      <p class="footer-copy">© Tarvenly Work Agency Ltd. | All rights reserved 2026</p>
    </footer>
  </article>

  <!-- Construction & Traders page -->
  <article class="page" style="left:48px;top:625px;height:542px">
    <div class="brand"><span class="brand-dot"></span><span class="brand-name">Tarvenly Work Agency Ltd.</span></div>
    <div class="topbar-phone"><svg width="4" height="4"><use href="#icon-phone"/></svg>Toll Free: 1-888-555-0142</div>
    <div class="topbar-register">Client Registration <svg width="6" height="3"><use href="#icon-arrow"/></svg></div>
    <nav class="main-nav"><span>Home</span><span class="is-active">Services</span><span>Candidates</span><span>Employers</span><span>About Us</span><span>Contact Us</span></nav>
    <div class="hero hero--construction" role="img" aria-label="Tower cranes over buildings under construction at sunset"></div>
    <h1 class="hero-title">CONSTRUCTION &amp; TRADERS</h1>

    <h2 class="section-title" style="top:105px">Reliable Construction <span class="highlight">Talent</span></h2>
    <p class="lead" style="top:117px">Tarvenly Work Agency is a premiere construction staffing agency that can provide you with <b>reliable, experienced, and skilled</b> tradespeople for projects all over Canada. We provide these positions</p>
    <div class="service-cards" style="top:135px">
      <div class="service-card"><svg><use href="#icon-temp"/></svg>Temporary Positions</div>
      <div class="service-card"><svg><use href="#icon-hire"/></svg>Temporary-to-Hire</div>
      <div class="service-card"><svg><use href="#icon-perm"/></svg>Permanent Positions</div>
    </div>
    <h2 class="section-title" style="top:164px">We are Construction Staffing Advisors –</h2>
    <h2 class="section-title" style="top:176px"><span class="highlight">A Trade Ticket is not a Sticker !</span></h2>
    <p class="lead" style="top:189px">As specialists for more than 10 years, we have met the staffing demands on construction projects for Residential, Commercial &amp; specialist contractors, Retail and Institutional owners, Engineering consultancies, and Developers with skilled tradespeople and construction labour on-time and on-budget.</p>

    <div class="photo-frame" style="left:32px;top:224px;width:112px;height:80px"></div>
    <div class="photo" style="left:27px;top:220px;background:linear-gradient(135deg,#e08a3c,#f3c27a 35%,#5a6d7e 65%,#2e3c4a)" role="img" aria-label="Engineers in hard hats reviewing plans on a rooftop"></div>
    <h3 class="block-title" style="left:161px;top:210px">Construction Companies</h3>
    <p class="block-text" style="left:161px;top:220px;width:110px">Whether you are looking for reliable, experienced Laborers for a short-term contract, or a Project Manager for a large 3-year project, our recruiters are experts in providing a skilled workforce to get the job done right. Our construction database includes tens of thousands of qualified personnel, allowing us to respond quickly to your changing needs so you can maintain your project schedules and labour pricing. Our candidates undergo extensive screening and we stand behind every person we place. We focus on the people while you focus on the project at hand</p>
    <div class="cta" style="left:161px;top:294px">Request Staffing</div>

    <h3 class="block-title" style="left:27px;top:318px">Construction Candidates</h3>
    <p class="block-text" style="left:27px;top:327px;width:112px">Tarvenly Work Agency is firmly entrenched in construction projects all over Canada. We invest our time and resources back into the construction &amp; engineering community to ensure we maximize employment opportunities for you. We help organize and prepare your profile once you have submitted your resume and if applicable – your project list of construction achievements.<br><br>Our clients appreciate our industry expertise and the thorough screening process we do to ensure a good fit. We may be bit tougher with our expectations, but we also stand behind every person we place</p>
    <div class="cta" style="left:27px;top:418px">Apply for jobs</div>
    <div class="photo-frame" style="left:154px;top:331px;width:112px;height:89px"></div>
    <div class="photo" style="left:159px;top:327px;height:89px;background:linear-gradient(135deg,#7f97ad,#b9c7d3 40%,#e07a2c 60%,#4a5560)" role="img" aria-label="Ironworkers in hard hats on a high-rise steel frame"></div>

    <footer class="site-footer" style="top:440px">
      <div class="footer-brand"><span class="brand-name">Tarvenly Work Agency Ltd.</span><div class="footer-social"><span></span><span></span></div></div>
      <div class="footer-col" style="left:94px"><h4 class="footer-heading">Quick Links</h4><ul class="footer-links"><li>Home</li><li>Services</li><li>Candidates</li><li>Employers</li><li>About us</li><li>Contact us</li></ul></div>
      <div class="footer-col" style="left:147px"><h4 class="footer-heading">Our Services</h4><ul class="footer-links"><li>Oil, Gas and Mining</li><li>Administrative</li><li>Construction and Trades</li><li>Warehouse and Logistics</li><li>Manufacturing.</li></ul></div>
      <div class="footer-col" style="left:217px"><h4 class="footer-heading">Our Address</h4><ul class="footer-address"><li><svg><use href="#icon-building"/></svg>410 217 6 Ave SW Calgary,<br>AB, T2P 1K3</li><li><svg><use href="#icon-phone"/></svg>Toll-Free: 1-888-555-0142</li><li><svg><use href="#icon-phone"/></svg>403-555-0187</li></ul></div>
      <p class="footer-copy">© Tarvenly Work Agency Ltd. | All rights reserved 2026</p>
    </footer>
  </article>

  <!-- Administrative page -->
  <article class="page" style="left:365px;top:625px;height:529px">
    <div class="brand"><span class="brand-dot"></span><span class="brand-name">Tarvenly Work Agency Ltd.</span></div>
    <div class="topbar-phone"><svg width="4" height="4"><use href="#icon-phone"/></svg>Toll Free: 1-888-555-0142</div>
    <div class="topbar-register">Client Registration <svg width="6" height="3"><use href="#icon-arrow"/></svg></div>
    <nav class="main-nav"><span>Home</span><span class="is-active">Services</span><span>Candidates</span><span>Employers</span><span>About Us</span><span>Contact Us</span></nav>
    <div class="hero hero--admin" role="img" aria-label="Office team gathered around a laptop in a meeting"></div>
    <h1 class="hero-title">ADMINISTRATIVE</h1>

    <h2 class="section-title" style="top:105px">Administrative <span class="highlight">Excellence</span></h2>
    <p class="lead" style="top:117px">Tarvenly Work Agency Administrative and Clerical Staffing division was created to assist the growing requests from our clients in diverse industries. We provide a <b>reliable, experienced and professional</b> workforce for your <b>front and back-end office</b> needs with these positions</p>
    <div class="service-cards" style="top:141px">
      <div class="service-card"><svg><use href="#icon-temp"/></svg>Temporary Positions</div>
      <div class="service-card"><svg><use href="#icon-hire"/></svg>Temporary-to-Hire</div>
      <div class="service-card"><svg><use href="#icon-perm"/></svg>Permanent Positions</div>
    </div>
    <h2 class="section-title" style="top:170px">We are Administrative Staffing Advisors –</h2>
    <h2 class="section-title" style="top:182px"><span class="highlight">Efficiency, Reliability, Accountability</span></h2>
    <p class="lead" style="top:195px">As specialists for more than 10 years, we have met the staffing demands of small family-owned shops to some of Canada's largest companies providing them with the perfect candidates</p>

    <div class="photo-frame" style="left:32px;top:226px;width:112px;height:80px"></div>
    <div class="photo" style="left:27px;top:222px;background:linear-gradient(135deg,#5b6a7c,#1f2730 40%,#c9ccd1 70%,#8d9299)" role="img" aria-label="Group of office professionals posing at a conference table"></div>
    <h3 class="block-title" style="left:161px;top:215px">Companies</h3>
    <p class="block-text" style="left:161px;top:225px;width:110px">Whether you are looking for an experienced receptionist to act as an ambassador by welcoming people into your business, or an accounting and bookkeeping administrator who will organize your mountains of paperwork, our experienced staff will provide you with the best candidate.<br><br>Our registrant database includes thousands of qualified personnel allowing us to respond quickly to your changing needs. Candidates undergo extensive screening and we stand behind every person we place. We focus on the people while you focus on other priorities.</p>
    <div class="cta" style="left:161px;top:301px">Request Staffing</div>

    <h3 class="block-title" style="left:27px;top:332px">Administrative Candidates</h3>
    <p class="block-text" style="left:27px;top:341px;width:112px">Tarvenly Work Agency is firmly entrenched in small to large businesses all over Canada. We invest our time and resources back into the community to ensure we maximize employment opportunities for you. Our clients appreciate our industry expertise and the thorough screening process we do to ensure a good fit. We may be bit tougher with our expectations, but we also stand behind every person we place.</p>
    <div class="cta" style="left:27px;top:402px">Apply for jobs</div>
    <div class="photo-frame" style="left:154px;top:331px;width:112px;height:89px"></div>
    <div class="photo" style="left:159px;top:327px;height:89px;background:linear-gradient(135deg,#9fb3c2,#dfe6ea 40%,#c98a4a 65%,#3a3f47)" role="img" aria-label="Colleagues shaking hands in a glass-walled meeting room"></div>

    <footer class="site-footer" style="top:425px;height:104px">
      <div class="footer-brand"><span class="brand-name">Tarvenly Work Agency Ltd.</span><div class="footer-social"><span></span><span></span></div></div>
      <div class="footer-col" style="left:94px"><h4 class="footer-heading">Quick Links</h4><ul class="footer-links"><li>Home</li><li>Services</li><li>Candidates</li><li>Employers</li><li>About us</li><li>Contact us</li></ul></div>
      <div class="footer-col" style="left:147px"><h4 class="footer-heading">Our Services</h4><ul class="footer-links"><li>Oil, Gas and Mining</li><li>Administrative</li><li>Construction and Trades</li><li>Warehouse and Logistics</li><li>Manufacturing.</li></ul></div>
      <div class="footer-col" style="left:217px"><h4 class="footer-heading">Our Address</h4><ul class="footer-address"><li><svg><use href="#icon-building"/></svg>410 217 6 Ave SW Calgary,<br>AB, T2P 1K3</li><li><svg><use href="#icon-phone"/></svg>Toll-Free: 1-888-555-0142</li><li><svg><use href="#icon-phone"/></svg>403-555-0187</li></ul></div>
      <p class="footer-copy">© Tarvenly Work Agency Ltd. | All rights reserved 2026</p>
    </footer>
  </article>
</main>
</body>
</html>
```